Cedar Brook Stables, LLC

Equestrian business card to promote equine retirement, farm sitting, short term board. Located in Aiken, SC.
Updates
Updated color schemes.
Contact Information for Business Card
Contact info, description of work.
Colors
0094D4
00A9DD
6FCCEA
C7EBF8
E9F6FB
59FF00
82FF00
B8FF75
E3FFCB
F4FFEA
F0912C
F2A743
F7CA91
FBE8D2
FDF5EE

```html
<!DOCTYPE html>
<html lang="en">
<head>
<meta charset="utf-8">
<title>Cedar Brook Stables, LLC – Business Card</title>
<link href="https://fonts.googleapis.com/css2?family=Poppins:wght@400;500;600&display=swap" rel="stylesheet">
<style>
  :root {
    --page-bg: #f2f2f2;
    --card-white: #ffffff;
    --card-dark: #1e1b1c;
    --brand-green: #0b6e0b;
    --ink: #1a1a1a;
    --ink-light: #d9d9d9;
    --sun-yellow: #f7cf1e;
    --rule: #8a8a8a;
  }
  * { margin: 0; padding: 0; box-sizing: border-box; }
  html, body { width: 1065px; height: 1200px; overflow: hidden; }
  body {
    background: var(--page-bg);
    font-family: "Poppins", sans-serif;
    position: relative;
  }
  .card {
    position: absolute;
    width: 583px;
    height: 362px;
  }
  .card--front {
    left: 292px; top: 218px;
    background: var(--card-white);
    border-radius: 0 181px 181px 0;
  }
  .card--back {
    left: 263px; top: 623px;
    background: var(--card-dark);
    border-radius: 181px 0 0 181px;
  }
  .brand {
    position: absolute;
    width: 220px;
    display: flex;
    flex-direction: column;
    align-items: center;
    gap: 14px;
  }
  .card--front .brand { left: 21px; top: 92px; }
  .card--back .brand { left: 55px; top: 98px; }
  .brand__mark {
    width: 96px; height: 96px;
    border-radius: 50%;
    border: 4px solid var(--brand-green);
  }
  .brand__name {
    font-weight: 600;
    font-size: 16px;
    letter-spacing: 1px;
    text-align: center;
    line-height: 1.3;
    color: var(--ink);
  }
  .card--back .brand__name { color: var(--ink-light); }
  .divider {
    position: absolute;
    left: 256px; top: 95px;
    width: 1px; height: 173px;
    background: var(--rule);
  }
  .contact {
    position: absolute;
    left: 276px; top: 92px;
    color: var(--ink);
  }
  .contact__name {
    font-weight: 600;
    font-size: 22px;
    line-height: 1.1;
    color: var(--brand-green);
    letter-spacing: 0.3px;
  }
  .contact__title {
    font-size: 16px;
    line-height: 1.2;
  }
  .contact__list {
    list-style: none;
    margin-top: 14px;
    font-size: 17px;
    line-height: 21px;
  }
  .contact__list li { display: flex; align-items: center; gap: 6px; }
  .contact__list svg { width: 15px; height: 15px; flex: none; }
  .contact__address {
    margin-top: 12px;
    font-size: 17px;
    line-height: 21px;
  }
  .services {
    position: absolute;
    left: 312px; top: 139px;
    list-style: none;
    color: var(--sun-yellow);
    font-weight: 500;
    font-size: 21px;
    line-height: 26.5px;
  }
</style>
</head>
<body>
  <section class="card card--front">
    <div class="brand">
      <div class="brand__mark"></div>
      <p class="brand__name">CEDAR BROOK STABLES, LLC</p>
    </div>
    <div class="divider"></div>
    <div class="contact">
      <h1 class="contact__name">MARCUS REED</h1>
      <p class="contact__title">Managing Director</p>
      <ul class="contact__list">
        <li>
          <svg viewBox="0 0 16 16" aria-hidden="true"><path fill="var(--brand-green)" d="M3.6 1.2l2.2 2.9-1.3 1.6c.9 2 2.5 3.6 4.5 4.6l1.6-1.3 2.9 2.2-1.2 2.3C7.3 13.7 2.3 8.7 1.3 2.4z"/><path fill="none" stroke="var(--brand-green)" stroke-width="1.3" d="M9 1.5a5.5 5.5 0 015.5 5.5M9 4.2A2.8 2.8 0 0111.8 7"/></svg>
          044-123 456 789
        </li>
        <li>
          <svg viewBox="0 0 16 16" aria-hidden="true"><rect x="0.5" y="3" width="15" height="10" fill="var(--brand-green)"/><path fill="none" stroke="#fff" stroke-width="1.2" d="M1 3.5l7 5.5 7-5.5M1 12.5l5-4.5M15 12.5l-5-4.5"/></svg>
          info@webname.com
        </li>
        <li>
          <svg viewBox="0 0 16 16" aria-hidden="true"><g fill="none" stroke="var(--brand-green)" stroke-width="1.4"><circle cx="8" cy="8" r="6.8"/><ellipse cx="8" cy="8" rx="3" ry="6.8"/><path d="M1.2 8h13.6M2.2 4.6h11.6M2.2 11.4h11.6M8 1.2v13.6"/></g></svg>
          www.websitename.com
        </li>
      </ul>
      <p class="contact__address">421, Address line goes here<br>45452,Country Name</p>
    </div>
  </section>

  <section class="card card--back">
    <div class="brand">
      <div class="brand__mark"></div>
      <p class="brand__name">CEDAR BROOK STABLES, LLC</p>
    </div>
    <ul class="services">
      <li>Short Term Board</li>
      <li>Farm Sitting</li>
      <li>Equine Retirement</li>
    </ul>
  </section>
</body>
</html>
```